Financial & Tax Strategies

need to get a word press site with existing domains and condense existing content on existing site, make new site dynamic, need mobile too......need to take info from my quorvia website and get modern, relevant site, less verbose on first page, way more things to click and engage people. Would like it to look like this , but with my color scheme and not quite as busy looking. I like much of the content on my tabs. Want maximize by seo capabilities on their as well. The number one thing I can say is to go to my existing website and get content, logo, etc there … www.pinegatelarkgroup.com .

Target Market(s)

Those 40 -65, business owners for at least 5 years. Higher net worth.

Number of Pages Required

5+ page

Font styles to use
Sans Serif

Colors
f04a50
e4daeb
ffffff

Requirements
Must have
• seo maximized, lots of places to click on to contact us, calls to action, relevant, conservative, want it to look like this and have the function as well.....slight variation on messaging, but like the simplicity on first view. https://www.dorrickvale.com/
Nice to have
• Some area along right side where videos we do will be.
Should not have
• feel too busy, but still have lots of opportunities to engage.

```html
<!DOCTYPE html>
<html lang="en">
<head>
<meta charset="utf-8">
<title>Pinegate Lark Group</title>
<link href="https://fonts.googleapis.com/css2?family=Lato:wght@400;700;900&family=Open+Sans:wght@400;600;700&display=swap" rel="stylesheet">
<style>
:root{
  --red:#ed1c24;
  --lavender:#e4daeb;
  --lavender-soft:#f1ebf5;
  --dark:#2f2f2f;
  --ink:#333;
  --white:#fff;
}
*{box-sizing:border-box;margin:0;padding:0}
html,body{width:1200px;height:3742px;overflow:hidden;background:var(--white)}
body{font-family:"Open Sans",Arial,sans-serif;color:var(--ink)}
.site-header{height:100px;display:flex;align-items:center;justify-content:space-between;padding:0 80px;background:var(--white)}
.menu-icon{width:26px;display:flex;flex-direction:column;gap:5px}
.menu-icon span{height:3px;background:#666;display:block}
.brand{display:flex;align-items:center;gap:12px;font-family:"Lato",sans-serif;font-weight:700;font-size:24px;line-height:1.05;color:#555}
.brand-mark{width:42px;height:42px;border-radius:50%;background:#777}
.call-now{display:flex;align-items:center;gap:10px;font-size:13px;color:var(--red);font-weight:700;line-height:1.2}
.call-now small{display:block;color:#444;font-weight:400}
.round-icon{width:30px;height:30px;border-radius:50%;background:var(--red);display:flex;align-items:center;justify-content:center;flex:none}
.hero{height:536px;position:relative;background:linear-gradient(135deg,#1d2228 0%,#4a4f55 45%,#8b8d8e 75%,#c9c6c0 100%)}
.hero-title{position:absolute;left:420px;top:232px;width:412px;height:145px;background:rgba(60,60,60,.55);color:var(--white);font-family:"Lato",sans-serif;font-weight:400;font-size:34px;line-height:1.3;text-align:center;display:flex;align-items:center;justify-content:center}
.intro{height:461px;display:flex;justify-content:space-between;padding:57px 83px 0 80px}
.intro-text{width:525px;font-size:14px;line-height:1.45;color:#444}
.intro-text p{margin-bottom:16px}
.intro-photo{width:493px;height:342px;background:linear-gradient(160deg,#8fa3b5,#d8e0e8 55%,#eef1f4)}
.observations{height:470px;background:var(--lavender-soft);display:flex;padding:50px 80px 0 37px;gap:40px}
.chart-frame{width:549px;height:344px;position:relative}
.screen{position:absolute;left:28px;top:0;width:493px;height:318px;background:#1a1a1a;border-radius:12px;padding:14px}
.screen svg{display:block;background:var(--white)}
.base{position:absolute;left:0;top:318px;width:549px;height:18px;background:linear-gradient(#d8d8d8,#9a9a9a);border-radius:0 0 20px 20px}
.obs-list h2{font-family:"Lato",sans-serif;font-weight:400;font-size:38px;color:#222;margin:28px 0 28px}
.obs-list li{list-style:none;display:flex;gap:12px;font-size:14px;line-height:1.4;color:#444;margin-bottom:18px;width:500px}
.tick{flex:none;width:18px;height:18px;background:var(--red);margin-top:2px}
.contact-band{height:192px;background:linear-gradient(90deg,#3a3a3a,#555 50%,#3a3a3a);color:var(--white);text-align:center;padding-top:28px}
.contact-band h2{font-family:"Lato",sans-serif;font-size:33px;font-weight:700}
.contact-row{display:flex;justify-content:center;gap:30px;margin:16px 0 14px;font-size:32px;font-weight:700;font-family:"Lato",sans-serif}
.contact-row > span{display:flex;align-items:center;gap:14px}
.contact-row .round-icon{width:58px;height:58px}
.contact-band p{font-size:19px;font-weight:700}
.strategies{height:392px;background:var(--white);padding-top:30px;text-align:center}
.strategies h2{font-family:"Lato",sans-serif;font-weight:400;font-size:34px;color:#222}
.strategy-cards{display:flex;gap:25px;justify-content:center;margin-top:30px}
.strategy-card{width:243px;height:222px;background:var(--white);border-radius:16px;box-shadow:0 0 14px rgba(0,0,0,.12);display:flex;flex-direction:column;align-items:center;justify-content:center;gap:16px;font-size:16px;color:#444;line-height:1.3;padding:0 18px}
.strategy-card.is-active{background:var(--red);color:var(--white);font-weight:600}
.band-title{height:57px;background:var(--dark);color:var(--white);font-family:"Lato",sans-serif;font-size:34px;display:flex;align-items:center;justify-content:center}
.media{height:546px;background:var(--lavender);padding-top:33px}
.media-cards{display:flex;justify-content:center;gap:27px}
.media-card{width:355px;height:361px;background:var(--white);padding:12px}
.media-thumb{height:208px}
.thumb-money{background:linear-gradient(#9aa3ab,#d7dadc)}
.thumb-video{background:linear-gradient(135deg,#5a6b78,#b9aa98)}
.thumb-radio{background:var(--white);display:flex;align-items:center;justify-content:center;font-family:"Lato",sans-serif;font-size:40px;font-weight:700;color:#444}
.media-card h3{font-family:"Lato",sans-serif;font-size:18px;margin:14px 0 8px;color:#222}
.media-card p{font-size:13px;line-height:1.35;color:#555;height:54px}
.more{display:inline-block;font-size:12px;border-bottom:2px solid #999;margin-top:10px;color:#333}
.pill{display:block;margin:44px auto 0;width:202px;height:40px;border-radius:20px;background:var(--red);color:var(--white);font-size:15px;font-weight:700;text-align:center;line-height:40px}
.testimonials{height:551px;background:var(--lavender-soft);padding-top:40px}
.testi-cards{display:flex;justify-content:center;gap:34px}
.testi-card{width:300px;height:341px;background:var(--white);border-radius:14px;box-shadow:0 0 12px rgba(0,0,0,.08);text-align:center;padding:30px 22px 0}
.avatar{width:96px;height:96px;border-radius:50%;margin:0 auto 16px;background:linear-gradient(#c8ccd0,#8a9096)}
.testi-card h3{font-family:"Lato",sans-serif;font-size:18px;color:#222}
.testi-card .role{font-size:13px;color:var(--red);margin:4px 0 10px}
.testi-card p{font-size:12.5px;line-height:1.35;color:#555}
.dots{display:flex;justify-content:center;gap:6px;margin-top:28px}
.dots i{width:8px;height:8px;border-radius:50%;background:#999}
.dots i.on{background:var(--red)}
.quick-email{display:flex;justify-content:center;gap:12px;margin-top:38px}
.quick-email .field{width:420px;height:38px;background:var(--white);border-radius:19px;font-size:13px;color:#777;padding:10px 20px}
.quick-email .pill{margin:0;width:160px;height:38px;line-height:38px}
.site-footer{height:324px;background:var(--dark);color:var(--white);display:flex;padding:50px 80px 0;gap:60px;font-size:13px;line-height:1.6}
.foot-brand{width:300px}
.foot-brand .brand{color:var(--white);margin-bottom:14px}
.foot-brand .brand-mark{background:#bbb}
.site-footer h4{font-size:15px;margin-bottom:12px;font-family:"Lato",sans-serif;border-bottom:2px solid var(--red);display:inline-block}
.foot-col{width:130px}
.foot-col ul{list-style:none}
.foot-col li::before{content:"\203A  ";color:var(--red)}
.foot-address{width:210px}
.foot-address div{display:flex;gap:10px;margin-bottom:6px}
.foot-address .dot{flex:none;width:12px;height:12px;background:#ccc;border-radius:50%;margin-top:5px}
.foot-form{width:300px}
.foot-inputs{display:flex;gap:6px;margin-bottom:8px}
.foot-inputs span,.foot-msg{background:#222;border:1px solid #555;color:#aaa;font-size:11px;padding:4px 8px;flex:1}
.foot-msg{display:block;height:80px}
.foot-form .pill{margin:12px 0 0;width:160px;height:34px;line-height:34px;font-size:13px}
.copyright{height:55px;display:flex;align-items:center;justify-content:space-between;padding:0 80px;font-size:12px;color:#444;background:var(--white)}
.socials{display:flex;gap:10px}
.socials i{width:24px;height:24px;border-radius:50%;background:var(--red)}
</style>
</head>
<body>
<header class="site-header">
  <div class="menu-icon"><span></span><span></span><span></span></div>
  <div class="brand"><span class="brand-mark"></span><span>Pinegate<br>Lark Group</span></div>
  <div class="call-now">
    <span class="round-icon"><svg width="14" height="14" viewBox="0 0 24 24"><path fill="#fff" d="M6.6 10.8c1.4 2.8 3.8 5.1 6.6 6.6l2.2-2.2c.3-.3.7-.4 1-.2 1.1.4 2.3.6 3.6.6.6 0 1 .4 1 1V20c0 .6-.4 1-1 1C10.6 21 3 13.4 3 4c0-.6.4-1 1-1h3.5c.6 0 1 .4 1 1 0 1.3.2 2.5.6 3.6.1.3 0 .7-.2 1z"/></svg></span>
    <span>Call us Now<small>916.555.0142</small></span>
  </div>
</header>

<section class="hero" role="img" aria-label="Photo of a hand writing on financial paperwork at a desk">
  <h1 class="hero-title">But 1 - 2% Fee Seems<br>Reasonable, Right?</h1>
</section>

<section class="intro">
  <div class="intro-text">
    <p>Did you know that if you net 5% in a year and your fee is 1%, your broker has taken 20% of your profits and all the money that you would make for decades after on that amount, PLUS he/she will take that much all the next subsequent years?</p>
    <p>When it comes to saving money, the Swiss are very astute. They hold dear the wealth-building concept and Power of Compounding Interest. Graphs can tell a thousand tales when it comes to your returns and the removal of the power of compounding interest with the introduction of fees. This particular graph is very telling of the impact of seemingly small fees. You can easily see how the various fees effect a portfolio over 30 years. What if we told you that most people don't know what they are being charged in fees from their advisors let alone all the hidden fees? We charge no fees. Our compensation is built into what is charged to you.</p>
    <p>Though you may not know how to back out how much you are actually paying in fees currently, Pinegate Lark Group gladly educates you on this. We want your business. Here is a look at what the fees are costing you. Only one of many ways we improve your returns more than Financial Advisors and Accountants can. Let's see just how those itzy bitzy fees decimate returns.</p>
  </div>
  <div class="intro-photo" role="img" aria-label="Photo of a businessman beside a rising bar graph"></div>
</section>

<section class="observations">
  <div class="chart-frame">
    <div class="screen">
      <svg width="465" height="290" viewBox="0 0 465 290">
        <g stroke="#e5e5e5" stroke-width="1">
          <line x1="50" y1="40" x2="450" y2="40"/><line x1="50" y1="95" x2="450" y2="95"/><line x1="50" y1="150" x2="450" y2="150"/><line x1="50" y1="205" x2="450" y2="205"/>
        </g>
        <line x1="50" y1="255" x2="450" y2="255" stroke="#888"/><line x1="50" y1="20" x2="50" y2="255" stroke="#888"/>
        <g font-size="9" fill="#666" font-family="Open Sans,sans-serif">
          <text x="18" y="43">$4m</text><text x="14" y="98">$3.1m</text><text x="14" y="153">$1.9m</text><text x="10" y="208">$900k</text>
          <text x="50" y="270">0</text><text x="115" y="270">5</text><text x="180" y="270">10</text><text x="248" y="270">15</text><text x="315" y="270">20</text><text x="382" y="270">25</text><text x="440" y="270">30</text>
        </g>
        <path d="M50 245 Q300 220 450 40" fill="none" stroke="#f26b24" stroke-width="2.5"/>
        <path d="M50 245 Q300 225 450 85" fill="none" stroke="#3aa34a" stroke-width="2.5"/>
        <path d="M50 245 Q300 232 450 135" fill="none" stroke="#3a7bd5" stroke-width="2.5"/>
        <path d="M50 245 Q300 240 450 185" fill="none" stroke="#333" stroke-width="2.5"/>
        <g font-size="8" fill="#fff" font-family="Open Sans,sans-serif">
          <rect x="355" y="14" width="80" height="22" fill="#f26b24"/><text x="360" y="28">Total Value $4.5m</text>
          <rect x="300" y="60" width="80" height="22" fill="#3aa34a"/><text x="305" y="74">Total Value $1.7m</text>
          <rect x="255" y="112" width="80" height="22" fill="#3a7bd5"/><text x="260" y="126">Total Value $1.0m</text>
          <rect x="125" y="160" width="80" height="22" fill="#333"/><text x="130" y="174">Total Value $1.0m</text>
        </g>
      </svg>
    </div>
    <div class="base"></div>
  </div>
  <div class="obs-list">
    <h2>Key Observations:</h2>
    <ul>
      <li><span class="tick"></span>About $3,500,000.00 difference between 0% &amp; 3% after 30 years.</li>
      <li><span class="tick"></span>About $1,000,000.00 difference between 0% &amp; 2% after 20 years.</li>
      <li><span class="tick"></span>About 50% more value between 0% &amp; 3% after only 15 years.</li>
      <li><span class="tick"></span>About $300,000.00 between 0% and 2% after only 10 years.</li>
      <li><span class="tick"></span>Again, this is just one of the many ways in which our strategies and products yield much better results than financial advisors and accountants. Don't pay for the Wall to Financial Advisor infrastructure with just ok returns, contact Pinegate Lark Group to get a fresh look at your future.....it is NEVER too late.</li>
    </ul>
  </div>
</section>

<section class="contact-band">
  <h2>Contact us at Sales</h2>
  <div class="contact-row">
    <span><span class="round-icon"><svg width="28" height="22" viewBox="0 0 28 22"><rect x="1" y="1" width="26" height="20" fill="#fff"/><path d="M1 1l13 11L27 1" fill="none" stroke="#ed1c24" stroke-width="2"/></svg></span>Sales@PinegateLark.com</span>
    <span><span class="round-icon"><svg width="26" height="26" viewBox="0 0 24 24"><path fill="#fff" d="M6.6 10.8c1.4 2.8 3.8 5.1 6.6 6.6l2.2-2.2c.3-.3.7-.4 1-.2 1.1.4 2.3.6 3.6.6.6 0 1 .4 1 1V20c0 .6-.4 1-1 1C10.6 21 3 13.4 3 4c0-.6.4-1 1-1h3.5c.6 0 1 .4 1 1 0 1.3.2 2.5.6 3.6.1.3 0 .7-.2 1z"/></svg></span>916.555.0142</span>
  </div>
  <p>We'll make your retirement yodel.</p>
</section>

<section class="strategies">
  <h2>Tax Strategies Accountants &amp; Financial Advisors Don't Have</h2>
  <div class="strategy-cards">
    <div class="strategy-card"><svg width="44" height="44" viewBox="0 0 44 44"><g fill="#ed1c24"><rect x="6" y="24" width="6" height="16"/><rect x="16" y="14" width="6" height="26"/><rect x="26" y="20" width="6" height="20"/><rect x="36" y="8" width="4" height="32"/><rect x="2" y="40" width="40" height="2"/></g></svg>Insuring Portfolios Against Market Crashes</div>
    <div class="strategy-card is-active"><svg width="44" height="44" viewBox="0 0 44 44" fill="none" stroke="#fff" stroke-width="2.5"><path d="M14 6v20h18l4 12M14 26l-4 12M6 38q16 6 32 0"/></svg>Seemingly Small Fees Devastate Retirements. We Don't Charge Them</div>
    <div class="strategy-card"><svg width="44" height="44" viewBox="0 0 44 44" fill="none" stroke="#ed1c24" stroke-width="2.5"><rect x="4" y="8" width="34" height="28"/><path d="M10 15h22M10 21h10M10 27h10M24 21h8v6h-8z"/></svg>Business Owners &amp; Executives Love Our Tax &amp; Bonus Strategies!</div>
    <div class="strategy-card"><svg width="44" height="44" viewBox="0 0 44 44"><circle cx="22" cy="14" r="8" fill="#ed1c24"/><path d="M22 22v12M22 30l-7-5M22 28l7-5" stroke="#ed1c24" stroke-width="2.5" fill="none"/><rect x="12" y="34" width="20" height="6" fill="#ed1c24"/></svg>401k, Mutual Fund &amp; IRA Myths Revealed</div>
  </div>
</section>

<div class="band-title">Blogs, Videos &amp; Radio</div>
<section class="media">
  <div class="media-cards">
    <article class="media-card">
      <div class="media-thumb thumb-money" role="img" aria-label="Photo of a businessman with money falling around him"></div>
      <h3>Money Blog</h3>
      <p>Lorem Ipsum is simply dummy the printing and typesetting industry. Lorem Ipsum has been the in the standard dummy.</p>
      <span class="more">Continue..</span>
    </article>
    <article class="media-card">
      <div class="media-thumb thumb-video" role="img" aria-label="Photo of a smiling older businessman"></div>
      <h3>PLG Videos</h3>
      <p>Lorem Ipsum is simply dummy the printing and typesetting industry. Lorem Ipsum has been the in the standard dummy.</p>
      <span class="more">Continue..</span>
    </article>
    <article class="media-card">
      <div class="media-thumb thumb-radio">Crestwave Radio</div>
      <h3>Crestwave Radio</h3>
      <p>Catch us on Crestwave Radio's Della Farnsby Show KVRL Talk 820 am<br>(Steady Sam &amp; Practical Pete)</p>
      <span class="more">Continue..</span>
    </article>
  </div>
  <span class="pill">401k Facts</span>
</section>

<div class="band-title">Testimonials</div>
<section class="testimonials">
  <div class="testi-cards">
    <article class="testi-card">
      <div class="avatar" role="img" aria-label="Portrait photo of client"></div>
      <h3>Reid Halvorsen</h3><div class="role">CEO</div>
      <p>National Commerce Alliance Turnaround CEO of the Year<br>"I'm a CFO by trade. PLG has strategies for families, executive &amp; business owners that accountants and financial advisors don't have. Highest recommendation</p>
    </article>
    <article class="testi-card">
      <div class="avatar" role="img" aria-label="Portrait photo of client"></div>
      <h3>Milo Tressler</h3><div class="role">Probate Attorney</div>
      <p>Probate Attorney "As an attorney, my job is to weigh risk. As an investor, weighing risk and reward is even more important. As someone retiring in next 15 years, I wanted to eliminate the risks of a stock market crash. PLG does this better than any other company.</p>
    </article>
    <article class="testi-card">
      <div class="avatar" role="img" aria-label="Portrait photo of client"></div>
      <h3>Owen Ashcombe</h3><div class="role">Doctor</div>
      <p>Doctor "Being a doctor requires attention to detail. Pinegate Lark Group helped navigate and educate me on exactly how to decipher my portfolio statement. I would have changed 10 years ago if I would have known what I know now about money. Call them; you'll be happy you did</p>
    </article>
  </div>
  <div class="dots"><i></i><i class="on"></i><i></i></div>
  <div class="quick-email"><span class="field">Shoot us a quick email here</span><span class="pill">Submit</span></div>
</section>

<footer class="site-footer">
  <div class="foot-brand">
    <div class="brand"><span class="brand-mark"></span><span>Pinegate<br>Lark Group</span></div>
    <p>Pinegate Lark Group Bringing sensibility, predictability and peace of mind in retirement. We will do things for your financial lives accountants and financial advisors won't and can't.</p>
  </div>
  <div class="foot-col"><h4>Quick Link</h4><ul><li>Home</li><li>About us</li><li>Services</li><li>Blogs</li><li>Testimonials</li><li>Contact us</li></ul></div>
  <div class="foot-address"><h4>Address</h4>
    <div><span class="dot"></span><span>4821 Marrow Creek Lane,<br>Alder Hollow,<br>CA 95999</span></div>
    <div><span class="dot"></span><span>916.555.0142</span></div>
    <div><span class="dot"></span><span>Sales@PinegateLark.com</span></div>
  </div>
  <div class="foot-form"><h4>Contact us</h4>
    <div class="foot-inputs"><span>Name</span><span>Email</span><span>Phone</span></div>
    <span class="foot-msg">Message</span>
    <span class="pill">Baby Boomer Edition</span>
  </div>
</footer>
<div class="copyright"><span>CopyRight © 2019 Pinegate Lark Group. All Right Reserve</span><div class="socials"><i></i><i></i><i></i><i></i><i></i></div></div>
</body>
</html>
```